Disposable Mini Sauce Pot Design for Asian Chain Food Brands

We operate a Hainan Chicken Rice takeout brand under the name Brindle4U, with our official website: www.Brindle4U.example.
We offer four signature house sauces and are launching brand-new packaging for our sauce line. We require custom graphic designs exclusively for the sauce cup lids.
Product Material & Base Specs
The sauce cups are made of PP plastic, available in two translucent base options: Translucent White and Translucent Orange.
Four Sauce Varieties for Individual Lid Designs
1. Red Sauce – Fried Sweet Chili Sauce
2.Green Sauce – Scallion Oil Dressing
3.Sweet Soy Sauce
4.Sweet Red Sauce (Special for Fried Chicken)
Differentiate each sauce lid design through unique graphics, typography, or illustrative elements for easy customer identification.
The marking NET WT 2 OZ must be clearly printed on every lid.
**There is no need to print full descriptive text or the full name of the sauces on each lid; the design only needs to clearly differentiate the four sauce varieties.
**Please reference the original design style and brand color palette shown on our official website, and feel free to fully unleash your creativity.
Look and feel
Each slider illustrates characteristics of the customer's brand and the style your logo design should communicate.

```html
<!DOCTYPE html>
<html lang="en">
<head>
<meta charset="utf-8">
<title>Brindle4U Sauce Lids</title>
<link rel="stylesheet" href="https://fonts.googleapis.com/css2?family=Fira+Sans:wght@400;700;800&display=swap">
<style>
  :root {
    --lid-orange: #ff4a07;
    --chili-band: #fca203;
    --green-band: #a9ff0a;
    --soy-band: #4f1412;
    --red-band: #990000;
    --ink-white: #ffffff;
    --page: #ffffff;
  }
  html, body {
    margin: 0;
    padding: 0;
    width: 1200px;
    height: 1000px;
    overflow: hidden;
    background: var(--page);
  }
  .sheet {
    position: relative;
    width: 1200px;
    height: 1000px;
    font-family: "Fira Sans", sans-serif;
    color: var(--ink-white);
  }
  .lid {
    position: absolute;
    width: 287px;
    height: 325px;
    background: var(--lid-orange);
    border-radius: 46px;
    overflow: hidden;
    box-shadow: 0 2px 5px rgba(0, 0, 0, 0.28);
  }
  .lid--chili { left: 282px; top: 142px; }
  .lid--green { left: 631px; top: 142px; }
  .lid--soy   { left: 282px; top: 532px; }
  .lid--red   { left: 631px; top: 532px; }

  .flavour-band {
    position: absolute;
    left: 0;
    top: 25px;
  }
  .lid--chili .flavour-band { width: 219px; height: 180px; background: var(--chili-band); }
  .lid--green .flavour-band { width: 225px; height: 65px; background: var(--green-band); }
  .lid--soy .flavour-band   { width: 219px; height: 125px; background: var(--soy-band); }
  .lid--red .flavour-band   { width: 220px; height: 125px; background: var(--red-band); }

  .line {
    position: absolute;
    left: 27px;
    margin: 0;
    line-height: 1;
    white-space: nowrap;
  }
  .flavour-word, .sauce-word {
    font-weight: 700;
    font-size: 60px;
    letter-spacing: -0.5px;
  }
  .sauce-word { font-size: 62px; }
  .net-weight {
    font-weight: 700;
    font-size: 32px;
    letter-spacing: 0.3px;
  }
  .note {
    font-weight: 400;
    font-size: 23px;
    letter-spacing: 0.4px;
  }
  .brand-seal {
    position: absolute;
    left: 223px;
    top: 251px;
    width: 50px;
    height: 50px;
    border-radius: 50%;
    background: var(--ink-white);
    display: flex;
    align-items: center;
    justify-content: center;
    font-weight: 700;
    font-size: 9.5px;
    color: var(--lid-orange);
  }
</style>
</head>
<body>
<main class="sheet">

  <section class="lid lid--chili" aria-label="Fried Sweet Chili Sauce lid">
    <div class="flavour-band"></div>
    <p class="line flavour-word" style="top:27px">FRIED</p>
    <p class="line flavour-word" style="top:83px">SWEET</p>
    <p class="line flavour-word" style="top:139px">CHILI</p>
    <p class="line sauce-word" style="top:204px">SAUCE</p>
    <p class="line net-weight" style="top:267px">NET WT 2 OZ</p>
    <div class="brand-seal">Brindle4U</div>
  </section>

  <section class="lid lid--green" aria-label="Green Sauce lid">
    <div class="flavour-band"></div>
    <p class="line flavour-word" style="top:27px">GREEN</p>
    <p class="line sauce-word" style="top:89px">SAUCE</p>
    <p class="line net-weight" style="top:152px">NET WT 2 OZ</p>
    <p class="line note" style="top:241px">Scallion Oil</p>
    <p class="line note" style="top:270px">Dressing</p>
    <div class="brand-seal">Brindle4U</div>
  </section>

  <section class="lid lid--soy" aria-label="Sweet Soy Sauce lid">
    <div class="flavour-band"></div>
    <p class="line flavour-word" style="top:27px">SWEET</p>
    <p class="line flavour-word" style="top:82px">SOY</p>
    <p class="line sauce-word" style="top:149px">SAUCE</p>
    <p class="line net-weight" style="top:213px">NET WT 2 OZ</p>
    <div class="brand-seal">Brindle4U</div>
  </section>

  <section class="lid lid--red" aria-label="Sweet Red Sauce lid">
    <div class="flavour-band"></div>
    <p class="line flavour-word" style="top:27px">SWEET</p>
    <p class="line flavour-word" style="top:82px">RED</p>
    <p class="line sauce-word" style="top:149px">SAUCE</p>
    <p class="line net-weight" style="top:213px">NET WT 2 OZ</p>
    <p class="line note" style="top:246px">Special for</p>
    <p class="line note" style="top:273px">Fried Chicken</p>
    <div class="brand-seal">Brindle4U</div>
  </section>

</main>
</body>
</html>
```